Agrarhandel benötigt Homepage
Zielgruppe
Wir sind ein Agrarhandel mit einem Warenumschlagslager im Sinne eines klassischen Einzelhandels und vertreiben Produkte an Landwirte.
Wir vertreiben folgende Hauptproduktgruppen:
Einzelfuttermittel
wie z.B. Sojaexktraktionsschrot. Die einzelnen Produkte könnten z.B. wie die Futtermittel auf folgender Seite dargestellt werden (https://www.kornprobe-beispiel.eu/de/produkt/trelomixan)
Mischfuttermittel
Hier bieten wir unseren Kunden an, individuelles Mischfutter auf Basis unserer Einzelfuttermittel herzustellen.
Weitere Details und weitere Produktbereiche habe ich in einer Powerpoint-Übersicht dargestellt.
Neben diesen Produkten wollen wir uns als Familienunternehmen selbst vorstellen. Zudem betreiben wir in unserer Familie zusätzlich einen Milchviehbetrieb den wir ebenfalls hervorheben möchten, da wir unseren Kunden gegenüber einerseits als Zulieferer aber auch als Kollege auftreten wollen.
Einzelfuttermittel: Hier können wir durch unsere Unabhängigkeit punkten, da wir nicht abhängig von bestimmten Lieferanten sind und dementsprechend unabhängig beraten können. Wir untersuchen im Vergleich zu unseren Wettbewerben die Qualität der Futtermittel bis ins Detail und können daher eine Transparenz bieten, die Konkurrenten in der Regel nicht bieten können. Unser Warenumschlagsplatz mit moderner Technik ermöglicht es uns äußerst kosteneffizient die Waren umschlagen und ausliefern zu können.
Mischfuttermittel: Auf Basis der vorhandenen Einzelfuttermittel stellen wir je nach Kundenwunsch individuelle Mischfutter her. Wir arbeiten mit offenen Deklarationen, sodass unsere Kunden jederzeit nachvollziehen können, ob auch die Einzelfuttermittel verwendet wurden, die sie bestellt haben und keine billigen Ersatzprodukte verwendet wurden.
Zudem sind wir BT und HUPA zertifiziert. Die aktuellen für unser Unternehmen ausgestellten Zertifikate müssen für unsere Kunden als Download zur Verfügung stehen. Statt dem HUPA-Logo bitte das ..
Aufgabenstellung
Wir möchten gerne ein zeitgemäße Homepage, jedoch muss auch berücksichtigt werden, dass unsere Kunden eher konservativ denken.

```html
<!DOCTYPE html>
<html lang="de">
<head>
<meta charset="utf-8">
<title>Talgrund Agrar – Startseite</title>
<link href="https://fonts.googleapis.com/css2?family=DM+Sans:wght@400;500;700&display=swap" rel="stylesheet">
<style>
:root{
  --green:#1c6b54;
  --orange:#fbb12b;
  --ink:#2b2622;
  --sky:#ecebe7;
  --field-mid:#b69a76;
  --field-dark:#4a2e18;
  --side:#3a2415;
  --gap:#ffffff;
}
*{margin:0;padding:0;box-sizing:border-box}
html,body{width:1200px;height:3104px;overflow:hidden;background:var(--gap);font-family:"DM Sans",sans-serif;color:var(--ink)}
.slide{position:relative;width:1200px;height:758px;overflow:hidden;margin-bottom:24px}
.slide:last-child{margin-bottom:0}
.hero-photo{position:absolute;inset:0;background:
  radial-gradient(ellipse 260px 380px at 1030px 560px,rgba(40,22,10,.85),rgba(40,22,10,0) 70%),
  radial-gradient(ellipse 110px 150px at 540px 590px,rgba(45,25,12,.8),rgba(45,25,12,0) 70%),
  linear-gradient(180deg,var(--sky) 0%,#e6e2db 48%,var(--field-mid) 66%,#7c5a3a 82%,var(--field-dark) 100%)}
.site-nav{position:absolute;top:24px;left:80px;right:81px;height:26px;display:flex;align-items:center}
.brand-small{font-weight:700;font-size:15px;color:var(--ink);display:flex;align-items:center;gap:8px;margin-top:6px}
.brand-small .dot{width:12px;height:12px;border-radius:50%;background:var(--green)}
.menu{margin-left:auto;display:flex;align-items:center;font-size:11.5px;text-transform:uppercase;letter-spacing:.2px}
.menu a{color:var(--ink);text-decoration:none;margin-left:25px}
.menu .btn-prices{background:var(--orange);color:#fff;padding:6px 18px;margin-left:26px;width:97px;text-align:center}
.brand-large{position:absolute;left:78px;top:318px;font-weight:700;font-size:52px;color:var(--green);letter-spacing:-.5px;display:flex;align-items:center;gap:16px}
.brand-large .mark{width:22px;height:22px;background:var(--orange)}
.divider{position:absolute;left:80px;right:81px;top:312px;height:2px;background:var(--green)}
.feature{position:absolute;left:761px;top:182px;width:360px}
.feature .icon{position:absolute;left:0;top:0;width:42px;height:46px}
.feature h2{margin-left:53px;font-size:21px;font-weight:700;color:var(--green);line-height:34px}
.feature p{margin-left:53px;margin-top:6px;font-size:13px;line-height:17px;color:#33302b}
.scroll-hint{position:absolute;left:586px;top:706px;width:28px;height:42px}
.contact-rail{position:absolute;right:0;top:574px;width:54px;display:flex;flex-direction:column;gap:6px}
.contact-rail a{display:flex;align-items:center;justify-content:center;height:54px;background:var(--side)}
</style>
</head>
<body>

<section class="slide">
  <div class="hero-photo" role="img" aria-label="Rinder auf einer Weide im Abendlicht"></div>
  <nav class="site-nav">
    <div class="brand-small"><span class="dot"></span>Talgrund Agrar</div>
    <div class="menu"><a href="#">Über uns</a><a href="#">Produkte ⌄</a><a href="#">Partner</a><a href="#">Downloads</a><a href="#">Kontakt</a><a href="#" class="btn-prices">Preisliste</a></div>
  </nav>
  <div class="divider"></div>
  <div class="brand-large"><span class="mark"></span>TALGRUND AGRAR</div>
  <div class="feature">
    <svg class="icon" viewBox="0 0 42 46"><circle cx="20" cy="20" r="19" fill="var(--green)"/><circle cx="20" cy="20" r="14" fill="none" stroke="#fff" stroke-width="2"/><path d="M13 20l5 5 9-10" fill="none" stroke="#fff" stroke-width="3"/></svg>
    <h2>Premium Qualität</h2>
    <p>Unsere Futtermittel unterliegen strengen Qualitätsprüfungen, um höchste Standards zu gewährleisten.</p>
  </div>
  <svg class="scroll-hint" viewBox="0 0 28 42"><rect x="2" y="2" width="24" height="38" rx="12" fill="none" stroke="#fff" stroke-width="2"/><path d="M14 9v18M8 21l6 6 6-6" fill="none" stroke="#fff" stroke-width="2"/></svg>
  <div class="contact-rail">
    <a href="#" aria-label="E-Mail"><svg width="26" height="18" viewBox="0 0 26 18"><rect x="1" y="1" width="24" height="16" fill="none" stroke="#fff" stroke-width="2"/><path d="M1 1l12 9 12-9" fill="none" stroke="#fff" stroke-width="2"/></svg></a>
    <a href="#" aria-label="Telefon"><svg width="16" height="26" viewBox="0 0 16 26"><rect x="1" y="1" width="14" height="24" rx="2" fill="none" stroke="#fff" stroke-width="2"/><circle cx="8" cy="21" r="1.5" fill="#fff"/></svg></a>
    <a href="#" aria-label="Nachricht"><svg width="24" height="24" viewBox="0 0 24 24"><circle cx="12" cy="12" r="10" fill="none" stroke="#fff" stroke-width="2"/></svg></a>
  </div>
</section>

<section class="slide">
  <div class="hero-photo" role="img" aria-label="Rinder auf einer Weide im Abendlicht"></div>
  <nav class="site-nav">
    <div class="brand-small"><span class="dot"></span>Talgrund Agrar</div>
    <div class="menu"><a href="#">Über uns</a><a href="#">Produkte ⌄</a><a href="#">Partner</a><a href="#">Downloads</a><a href="#">Kontakt</a><a href="#" class="btn-prices">Preisliste</a></div>
  </nav>
  <div class="divider"></div>
  <div class="brand-large"><span class="mark"></span>TALGRUND AGRAR</div>
  <div class="feature">
    <svg class="icon" viewBox="0 0 42 46"><path d="M8 28l-4 14 8-4 5 5 3-13zM34 28l4 14-8-4-5 5-3-13z" fill="var(--green)"/><circle cx="21" cy="17" r="16" fill="var(--green)"/><circle cx="21" cy="17" r="10" fill="none" stroke="#fff" stroke-width="2"/></svg>
    <h2>Geprüft und Zertifiziert</h2>
    <p>Wir sind stolz, BT- und HUPA-zertifiziert zu sein – Ihr Vertrauen in unsere Produkte ist dennoch unsere höchste Auszeichnung.</p>
  </div>
  <svg class="scroll-hint" viewBox="0 0 28 42"><rect x="2" y="2" width="24" height="38" rx="12" fill="none" stroke="#fff" stroke-width="2"/><path d="M14 9v18M8 21l6 6 6-6" fill="none" stroke="#fff" stroke-width="2"/></svg>
  <div class="contact-rail">
    <a href="#" aria-label="E-Mail"><svg width="26" height="18" viewBox="0 0 26 18"><rect x="1" y="1" width="24" height="16" fill="none" stroke="#fff" stroke-width="2"/><path d="M1 1l12 9 12-9" fill="none" stroke="#fff" stroke-width="2"/></svg></a>
    <a href="#" aria-label="Telefon"><svg width="16" height="26" viewBox="0 0 16 26"><rect x="1" y="1" width="14" height="24" rx="2" fill="none" stroke="#fff" stroke-width="2"/><circle cx="8" cy="21" r="1.5" fill="#fff"/></svg></a>
    <a href="#" aria-label="Nachricht"><svg width="24" height="24" viewBox="0 0 24 24"><circle cx="12" cy="12" r="10" fill="none" stroke="#fff" stroke-width="2"/></svg></a>
  </div>
</section>

<section class="slide">
  <div class="hero-photo" role="img" aria-label="Rinder auf einer Weide im Abendlicht"></div>
  <nav class="site-nav">
    <div class="brand-small"><span class="dot"></span>Talgrund Agrar</div>
    <div class="menu"><a href="#">Über uns</a><a href="#">Produkte ⌄</a><a href="#">Partner</a><a href="#">Downloads</a><a href="#">Kontakt</a><a href="#" class="btn-prices">Preisliste</a></div>
  </nav>
  <div class="divider"></div>
  <div class="brand-large"><span class="mark"></span>TALGRUND AGRAR</div>
  <div class="feature">
    <svg class="icon" viewBox="0 0 42 46"><rect x="2" y="14" width="18" height="18" fill="var(--green)"/><rect x="22" y="2" width="18" height="18" fill="var(--green)"/><rect x="22" y="22" width="14" height="14" fill="var(--green)"/><rect x="6" y="34" width="14" height="8" fill="var(--green)"/></svg>
    <h2>Individuelles Mischfutter</h2>
    <p>Unsere Experten stellen Ihr Mischfutter nach Ihren Wünschen zusammen – für eine maßgeschneiderte Ernährung Ihres Tieres.</p>
  </div>
  <svg class="scroll-hint" viewBox="0 0 28 42"><rect x="2" y="2" width="24" height="38" rx="12" fill="none" stroke="#fff" stroke-width="2"/><path d="M14 9v18M8 21l6 6 6-6" fill="none" stroke="#fff" stroke-width="2"/></svg>
  <div class="contact-rail">
    <a href="#" aria-label="E-Mail"><svg width="26" height="18" viewBox="0 0 26 18"><rect x="1" y="1" width="24" height="16" fill="none" stroke="#fff" stroke-width="2"/><path d="M1 1l12 9 12-9" fill="none" stroke="#fff" stroke-width="2"/></svg></a>
    <a href="#" aria-label="Telefon"><svg width="16" height="26" viewBox="0 0 16 26"><rect x="1" y="1" width="14" height="24" rx="2" fill="none" stroke="#fff" stroke-width="2"/><circle cx="8" cy="21" r="1.5" fill="#fff"/></svg></a>
    <a href="#" aria-label="Nachricht"><svg width="24" height="24" viewBox="0 0 24 24"><circle cx="12" cy="12" r="10" fill="none" stroke="#fff" stroke-width="2"/></svg></a>
  </div>
</section>

<section class="slide">
  <div class="hero-photo" role="img" aria-label="Rinder auf einer Weide im Abendlicht"></div>
  <nav class="site-nav">
    <div class="brand-small"><span class="dot"></span>Talgrund Agrar</div>
    <div class="menu"><a href="#">Über uns</a><a href="#">Produkte ⌄</a><a href="#">Partner</a><a href="#">Downloads</a><a href="#">Kontakt</a><a href="#" class="btn-prices">Preisliste</a></div>
  </nav>
  <div class="divider"></div>
  <div class="brand-large"><span class="mark"></span>TALGRUND AGRAR</div>
  <div class="feature">
    <svg class="icon" viewBox="0 0 42 46"><circle cx="12" cy="12" r="11" fill="var(--green)"/><path d="M12 5v7h6" fill="none" stroke="#fff" stroke-width="2.5"/><ellipse cx="24" cy="32" rx="16" ry="11" fill="var(--green)"/><rect x="14" y="38" width="5" height="7" fill="var(--green)"/><rect x="29" y="38" width="5" height="7" fill="var(--green)"/></svg>
    <h2>Sparen Sie Zeit und Geld</h2>
    <p>Hochwertige Futtermittel, die Ihren Geldbeutel schonen. Zeit- und kosteneffiziente Liefermöglichkeiten für die optimale Versorgung Ihrer Tiere.</p>
  </div>
  <svg class="scroll-hint" viewBox="0 0 28 42"><rect x="2" y="2" width="24" height="38" rx="12" fill="none" stroke="#fff" stroke-width="2"/><path d="M14 9v18M8 21l6 6 6-6" fill="none" stroke="#fff" stroke-width="2"/></svg>
  <div class="contact-rail">
    <a href="#" aria-label="E-Mail"><svg width="26" height="18" viewBox="0 0 26 18"><rect x="1" y="1" width="24" height="16" fill="none" stroke="#fff" stroke-width="2"/><path d="M1 1l12 9 12-9" fill="none" stroke="#fff" stroke-width="2"/></svg></a>
    <a href="#" aria-label="Telefon"><svg width="16" height="26" viewBox="0 0 16 26"><rect x="1" y="1" width="14" height="24" rx="2" fill="none" stroke="#fff" stroke-width="2"/><circle cx="8" cy="21" r="1.5" fill="#fff"/></svg></a>
    <a href="#" aria-label="Nachricht"><svg width="24" height="24" viewBox="0 0 24 24"><circle cx="12" cy="12" r="10" fill="none" stroke="#fff" stroke-width="2"/></svg></a>
  </div>
</section>

</body>
</html>
```